Business Card - high end, modern health care

Hey designers!

We need a double sided business card for the boutique, cutting edge physical therapy rehabilitation centre in Sydney's Northern Beaches.

With the most qualified physios in the area The Harbourview Motion Clinic does what other physiotherapy practices do not, we take our time with our patients giving them longer appointments, better physios and therefor faster results!

We guarantee that the service people receive at THMC will be unparalleled.

Hence we need a business card to reflect our modern, boutique, high end service. The final design needs to reflect that we are in a class of our own yet with the feel of beachside retreat.

Below I have attached our logo in both blue on white and white on blue. The exact colour is;
and the font that we have used in our logo is Tex Gyre Aventador.

I like the idea of the blue as the main colour as it is more eye catching and our signage onto the main road will be in this blue and in the interest of consistency across marketing the blue needs to be a part of the design. However I would appreciate a few designs onto a wooden background as this is a visual theme within the fitout of the practice.

The design needs to be of standard size (91x55mm).

Target Market(s)

We target people who have an end outcome in mind and those who have had poor experiences with other providers and ensure that everyone gets the care that they deserve with a premium service that is tailored to the individuals circumstances. As a premium service, the target market is highly educated, business and tech savvy with the additional target market of elderly people who have self funded their retirement and see value in paying for the best ongoing rehabilitation to maintain independence.

Industry/Entity Type

Physical Therapy

Contact Information for Business Card

Name, designation( Titled Musculoskeletal Physiotherapist... there will also be those in the company that have multiple designations ie 5 or 6 words long), phone number, email, facebook, instagram, address

Font styles to use
Sans Serif

Colors

Designer to choose colors to be used in the design.

Requirements
Must have
• Front - The logo as large as possible, blue or wooden theme, and all of the important details.
• Back - A blank space/lines on which to write appointment times (no "Appointment, date, time" etc.)
Nice to have
• facebook url
• logos for facebook and instagram
• Mini logos for the phone and email?

```html
<!DOCTYPE html>
<html lang="en">
<head>
<meta charset="utf-8">
<title>The Harbourview Motion Clinic – Business Card</title>
<link rel="stylesheet" href="https://fonts.googleapis.com/css2?family=Lato:wght@400;700&display=swap">
<style>
  :root {
    --brand-blue: #0a4fa6;
    --ink: #1d1d1d;
    --paper: #ffffff;
    --backdrop: #676767;
    --divider: #d2d2d2;
  }
  * { box-sizing: border-box; margin: 0; padding: 0; }
  html, body { width: 1200px; height: 802px; overflow: hidden; }
  body {
    background: var(--backdrop);
    font-family: "Lato", sans-serif;
    position: relative;
  }
  .card {
    position: absolute;
    top: 274px;
    width: 443px;
    height: 265px;
    background: var(--paper);
    overflow: hidden;
  }
  .card--front { left: 136px; }
  .card--back { left: 624px; }

  /* Front */
  .brand {
    position: absolute;
    left: 40px;
    top: 40px;
    width: 144px;
    text-align: center;
  }
  .brand__disc {
    display: block;
    width: 112px;
    height: 112px;
    margin: 0 auto 10px;
    border-radius: 50%;
    background: var(--brand-blue);
  }
  .brand__name {
    color: var(--brand-blue);
    font-weight: 700;
    font-size: 13.5px;
    line-height: 1.15;
    letter-spacing: 0.3px;
  }
  .divider {
    position: absolute;
    left: 205px;
    top: 68px;
    width: 1px;
    height: 132px;
    background: var(--divider);
  }
  .details {
    position: absolute;
    left: 231px;
    top: 75px;
    color: var(--ink);
  }
  .details__name {
    color: var(--brand-blue);
    font-weight: 700;
    font-size: 16.5px;
    line-height: 1;
    letter-spacing: 0.2px;
  }
  .details__role {
    font-size: 12.5px;
    line-height: 1.2;
    margin-top: 2px;
  }
  .contact-list { list-style: none; margin-top: 9px; }
  .contact-list + .contact-list { margin-top: 9px; }
  .contact-list li {
    display: flex;
    align-items: center;
    gap: 4px;
    font-size: 12.8px;
    line-height: 16.5px;
  }
  .contact-list svg { width: 14px; height: 14px; flex: none; }
  .social-dot {
    width: 13px;
    height: 13px;
    border-radius: 50%;
    background: var(--brand-blue);
    flex: none;
    margin-right: 1px;
  }

  /* Back */
  .back__band {
    position: absolute;
    left: 0;
    width: 100%;
    background: var(--brand-blue);
  }
  .back__band--top { top: 0; height: 109px; }
  .back__band--bottom { top: 161px; height: 104px; }
  .appointment-line {
    position: absolute;
    left: 84px;
    top: 124px;
    display: flex;
    align-items: flex-end;
    font-weight: 700;
    font-size: 11.5px;
    color: #000;
  }
  .appointment-line__blank {
    display: inline-block;
    border-bottom: 1px solid #000;
    height: 10px;
    margin-bottom: 1px;
  }
  .appointment-line__blank--date { width: 107px; }
  .appointment-line__blank--time { width: 108px; }
</style>
</head>
<body>
  <section class="card card--front" aria-label="Business card front">
    <div class="brand">
      <span class="brand__disc"></span>
      <p class="brand__name">THE HARBOURVIEW<br>MOTION CLINIC</p>
    </div>
    <div class="divider"></div>
    <div class="details">
      <h1 class="details__name">MARCUS ELLERY</h1>
      <p class="details__role">Managing Director</p>
      <ul class="contact-list">
        <li>
          <svg viewBox="0 0 14 14" aria-hidden="true">
            <circle cx="7" cy="7" r="6.2" fill="none" stroke="#0a4fa6" stroke-width="1.2"/>
            <path d="M4.6 3.8c.4-.3.8-.2 1 .2l.6 1.1c.1.3 0 .6-.2.8l-.4.3c.4.9 1.1 1.6 2 2l.3-.4c.2-.2.5-.3.8-.2l1.1.6c.4.2.5.6.2 1-.5.7-1.2.9-2 .6-1.8-.7-3.2-2.1-3.9-3.9-.3-.8-.1-1.5.5-2.1z" fill="#0a4fa6"/>
          </svg>
          400 555 0192
        </li>
        <li>
          <svg viewBox="0 0 14 14" aria-hidden="true">
            <circle cx="7" cy="7" r="6.2" fill="none" stroke="#0a4fa6" stroke-width="1.2"/>
            <rect x="3.8" y="4.8" width="6.4" height="4.4" fill="#0a4fa6"/>
            <path d="M3.8 4.8 7 7.3l3.2-2.5" fill="none" stroke="#fff" stroke-width="0.8"/>
          </svg>
          info@harbourviewmotion.com
        </li>
      </ul>
      <ul class="contact-list">
        <li><span class="social-dot"></span>/harbourviewmotionclinic</li>
        <li><span class="social-dot"></span>@harbourviewmotionclinic</li>
      </ul>
    </div>
  </section>

  <section class="card card--back" aria-label="Business card back">
    <div class="back__band back__band--top" role="img" aria-label="Repeating brand pattern on blue"></div>
    <p class="appointment-line">
      DATE<span class="appointment-line__blank appointment-line__blank--date"></span>TIME<span class="appointment-line__blank appointment-line__blank--time"></span>
    </p>
    <div class="back__band back__band--bottom" role="img" aria-label="Repeating brand pattern on blue"></div>
  </section>
</body>
</html>
```